Card Design for my dog training business Brightpaw Obedience

Need a business card design for my dog training business with my new logo. Want the card to come off professional yet fun. Want it to be very eye catchy as well. I normally have these at vet clinics, pet stores, and groomers. so need it to look better than my competitors.
Target Market(s)
dog owners
Industry/Entity Type
Dog Training
Contact Information for Business Card
needs logo, my name and info
Font styles to use
Serif
Colors
0255a3
ffffff
ec1f27
000000
333333
fbfbfb
Requirements
Must have
- Brightpaw Obedience
- Felix Orland
- 415 903 2276
- info@brightpawobedience.example
- www.brightpawobedience.example

```html
<!DOCTYPE html>
<html lang="en">
<head>
<meta charset="utf-8">
<title>Brightpaw Obedience — Business Card</title>
<link rel="stylesheet" href="https://fonts.googleapis.com/css2?family=Crimson+Text:ital,wght@0,400;0,600;1,400&family=Lato:wght@400&display=swap">
<style>
  :root {
    --stage: #1e1e1e;
    --card-black: #171515;
    --card-white: #ffffff;
    --paper-soft: #fbfbfb;
    --ink: #000000;
    --ink-soft: #333333;
    --accent-red: #ec1f27;
    --light-text: #e6e6e6;
    --muted-text: #bdbdbd;
  }
  * { box-sizing: border-box; margin: 0; padding: 0; }
  html, body { width: 1200px; height: 900px; overflow: hidden; }
  body { background: var(--stage); position: relative; font-family: "Lato", sans-serif; }

  .card {
    position: absolute;
    left: 250px;
    width: 700px;
    height: 400px;
    overflow: hidden;
    box-shadow: 0 10px 30px rgba(0,0,0,.5);
  }
  .card--front { top: 33px; background: linear-gradient(160deg, var(--card-white) 30%, var(--paper-soft) 60%, #ececec 100%); }
  .card--back { top: 467px; background: var(--card-black); }

  .front__header { position: absolute; left: 46px; top: 34px; }
  .front__name {
    font-family: "Crimson Text", serif;
    font-weight: 400;
    font-size: 28px;
    letter-spacing: 1px;
    text-transform: uppercase;
    color: var(--accent-red);
    line-height: 1;
  }
  .front__role { margin-top: 6px; font-size: 19px; color: var(--ink-soft); }

  .front__panel {
    position: absolute;
    left: 0; top: 150px;
    width: 410px; height: 250px;
    background: var(--card-black);
    padding: 34px 0 0 46px;
    color: var(--light-text);
    font-size: 19px;
    line-height: 1.38;
  }
  .front__address { margin-bottom: 10px; }
  .contact-line { display: flex; align-items: center; gap: 10px; white-space: nowrap; }
  .contact-line svg { width: 13px; height: 13px; flex: none; fill: none; stroke: var(--muted-text); stroke-width: 1.6; }

  .front__brand {
    position: absolute;
    left: 440px; right: 30px; bottom: 40px;
    display: flex; align-items: center; justify-content: center; gap: 14px;
    font-family: "Crimson Text", serif;
    font-weight: 600;
    font-size: 34px;
    line-height: 1.05;
    color: var(--ink);
  }
  .front__brand-name { display: flex; flex-direction: column; }
  .brand-dot { width: 16px; height: 16px; border-radius: 50%; background: var(--ink); flex: none; }

  .back__brand {
    position: absolute; left: 0; right: 0; top: 130px;
    display: flex; justify-content: center; align-items: center; gap: 14px;
    font-family: "Crimson Text", serif;
    font-weight: 600;
    font-size: 44px;
    color: var(--light-text);
  }
  .back__brand .brand-dot { background: var(--light-text); width: 20px; height: 20px; }
  .back__rule { position: absolute; left: 230px; right: 230px; top: 212px; height: 1px; background: var(--muted-text); }
  .back__tagline {
    position: absolute; left: 0; right: 0; top: 232px;
    text-align: center;
    font-family: "Crimson Text", serif;
    font-style: italic;
    font-size: 18px;
    color: var(--muted-text);
  }
</style>
</head>
<body>
  <section class="card card--front">
    <header class="front__header">
      <h1 class="front__name">Felix Orland</h1>
      <p class="front__role">Managing Director</p>
    </header>

    <div class="front__panel">
      <p class="front__address">1208 Marlow Lane,<br>Eastbrook, 4417</p>
      <p class="contact-line">
        <svg viewBox="0 0 16 16"><path d="M4 2l2 3-1.5 1.5a8 8 0 0 0 5 5L11 10l3 2-1 2.5C7 14 2 9 1.5 3z"/></svg>
        415 903 2276
      </p>
      <p class="contact-line">
        <svg viewBox="0 0 16 16"><rect x="1.5" y="3.5" width="13" height="9"/><path d="M1.5 3.5l6.5 5 6.5-5"/></svg>
        info@brightpawobedience.example
      </p>
      <p class="contact-line">
        <svg viewBox="0 0 16 16"><circle cx="8" cy="8" r="6.5"/><path d="M1.5 8h13M8 1.5c3 3.5 3 9.5 0 13M8 1.5c-3 3.5-3 9.5 0 13"/></svg>
        www.brightpawobedience.example
      </p>
    </div>

    <div class="front__brand">
      <span class="brand-dot"></span>
      <span class="front__brand-name"><span>Brightpaw</span><span>Obedience</span></span>
    </div>
  </section>

  <section class="card card--back">
    <div class="back__brand">
      <span class="brand-dot"></span>
      <span>Brightpaw Obedience</span>
    </div>
    <div class="back__rule"></div>
    <p class="back__tagline">“Training dogs across the valley one dog at a time.”</p>
  </section>
</body>
</html>
```